Exciting & Elegant Stationary Pack

Stationary consists of
1. Letter head / Envelope
2. Business Card
3. Invoice
4. 40x40mm sticker

Attached files;

1. Logo (Other formats available on request)
2. MS word Doc - For information and description of design
3. Website image (This will be our new website so use the colours so everything ties together)
4. Sample of stationary pack we like, but feel free to be creative

Target Market(s)

Home improvement

Industry/Entity Type

Construction

Font styles to use
Other font styles liked:
• Leave up to designer - We like font used on (website attached image)

Requirements
Must have
• Please look at uploaded file of sample website and use colours
Nice to have
• Any type of business card design - eg. metal, die cut, embossed, etc...

```html
<!DOCTYPE html>
<html lang="en">
<head>
<meta charset="utf-8">
<title>Keystone Floors – Business Card</title>
<link href="https://fonts.googleapis.com/css2?family=Roboto:wght@300;400;700;900&display=swap" rel="stylesheet">
<style>
  :root {
    --navy: #0f4a6e;
    --navy-deep: #0b3c5a;
    --orange: #f0a06a;
    --ink: #4a5a66;
    --paper: #ffffff;
    --backdrop: #e9e6e1;
  }
  * { margin: 0; padding: 0; box-sizing: border-box; }
  html, body {
    width: 1200px; height: 950px; overflow: hidden;
    background: var(--backdrop);
    font-family: "Roboto", Arial, sans-serif;
  }
  .sheet { position: relative; width: 1200px; height: 950px; }
  .card {
    position: absolute; left: 220px; width: 760px; height: 434px;
    overflow: hidden;
    box-shadow: 0 6px 18px rgba(0,0,0,0.18);
  }
  .card--front { top: 30px; background: var(--paper); }
  .card--back { top: 486px; background: var(--navy); }

  .front-band { position: absolute; inset: 0; }

  .brand-name {
    position: absolute; left: 320px; top: 42px;
    color: var(--paper);
    font-weight: 900; font-size: 30px; line-height: 1; letter-spacing: 1px;
    text-transform: uppercase; white-space: nowrap;
  }

  .contact { position: absolute; left: 52px; bottom: 44px; }
  .contact__name { color: var(--navy); font-weight: 700; font-size: 30px; line-height: 1.1; }
  .contact__role { color: var(--orange); font-weight: 400; font-size: 19px; margin-top: 4px; }
  .contact__licence { color: var(--ink); font-weight: 300; font-size: 18px; margin-top: 10px; }
  .contact__list { list-style: none; margin-top: 10px; }
  .contact__item {
    display: flex; align-items: center; gap: 10px;
    color: var(--ink); font-weight: 300; font-size: 18px; line-height: 1.55;
  }
  .contact__icon { width: 16px; height: 16px; flex: none; }

  .back-mark {
    position: absolute; inset: 0;
    display: flex; align-items: center; justify-content: center; gap: 16px;
  }
  .back-mark__square { width: 30px; height: 30px; background: var(--paper); }
  .back-mark__name {
    color: var(--paper); font-weight: 900; font-size: 44px; letter-spacing: 1px;
    text-transform: uppercase; white-space: nowrap;
  }
</style>
</head>
<body>
<main class="sheet">

  <section class="card card--front" aria-label="Business card front">
    <svg class="front-band" viewBox="0 0 760 434" width="760" height="434" aria-hidden="true">
      <polygon points="300,0 760,0 760,90 240,180" fill="var(--navy)"/>
    </svg>
    <div class="brand-name">Keystone Floors</div>

    <div class="contact">
      <div class="contact__name">Linh Tran</div>
      <div class="contact__role">Project Manager</div>
      <div class="contact__licence">Lic No. 204519c</div>
      <ul class="contact__list">
        <li class="contact__item">
          <svg class="contact__icon" viewBox="0 0 16 16" aria-hidden="true">
            <rect x="3" y="1" width="10" height="14" rx="2" fill="none" stroke="var(--navy)" stroke-width="1.6"/>
            <rect x="6.5" y="12" width="3" height="1.2" fill="var(--navy)"/>
          </svg>
          0400 555 218
        </li>
        <li class="contact__item">
          <svg class="contact__icon" viewBox="0 0 16 16" aria-hidden="true">
            <rect x="1" y="3" width="14" height="10" fill="var(--navy)"/>
            <polyline points="1,3 8,9 15,3" fill="none" stroke="#fff" stroke-width="1.2"/>
          </svg>
          info@keystonefloors.com.au
        </li>
        <li class="contact__item">
          <svg class="contact__icon" viewBox="0 0 16 16" aria-hidden="true">
            <circle cx="8" cy="8" r="7" fill="var(--navy)"/>
            <ellipse cx="8" cy="8" rx="3" ry="7" fill="none" stroke="#fff" stroke-width="1"/>
            <line x1="1" y1="8" x2="15" y2="8" stroke="#fff" stroke-width="1"/>
          </svg>
          www.keystonefloors.com.au
        </li>
      </ul>
    </div>
  </section>

  <section class="card card--back" aria-label="Business card back">
    <div class="back-mark">
      <span class="back-mark__square"></span>
      <span class="back-mark__name">Keystone Floors</span>
    </div>
  </section>

</main>
</body>
</html>
```